Wordpress Theme for Cedarline Clinics

** Please view updated Sitemap2.pdf doc to clarify some confusion ***

This is a multiuser WordPress subscription site for Cedarline Clinics. Please see attachment for sitemap. Please do not include extra content like social media icons, search bars, or images. If you have questions, please ask for clarification.
The site contains the following pages and sub-pages:

1. Home
2. Our Clinic
2a. Our Clinic > Mission
2b. Our Clinic > Services
2c. Our Clinic > Clinic Policies
2d. Our Clinic > Schedules
3. Our Staff
3a. Our Staff > [Staff member page]
4. Resources
4a. Resources > Patient Health (index)
4b. Resources > Patient Health (index) > [post]
4c. Resources > Links
4d. Resources > Forms
5. Alerts
5a. Alerts > [Alert Page]
6. Contact Us

Includes the Following Pages, Subpages, and Content
1. Home
a. About Us
b. Our Staff
c. Bulletins
d. Accepting New Patients (shown as an alert widget)
e. Links
i. Physician Toolbox
ii. Book an Appointment
f. Clinic Policies
i. Show first 3 policies (e.g. Late Arrivals, Missed Appointments, Fees)
ii. Link to Clinic Policies page
g. Primary widget (displayed on all pages)
i. Hours of operation
ii. Contact Info
1. Tel
2. Fax
3. Email
4. Address
5. Get directions (link to Google Maps)
2. Our Clinic
a. Main Page
i. Clinic Name
ii. Overview
iii. Languages Spoken
iv. Secondary Navigation
1. Mission
2. Services
3. Clinic Policies
4. Schedules (see attachment)
b. Our Clinic > Mission
c. Our Clinic > Services
i. For each service include service TITLE and DESCRIPTION
d. Our Clinic > Clinic Policies
i. For each policy include policy TITLE and DESCRIPTION
ii. Include the following policies in mockup
1. Late arrivals
2. Missed appointments
3. Fees for missed appointments
4. Referrals and follow-ups
5. Services not covered by RDA
6. Information for LTF patients
7. Medical Legal Reports
e. Our Clinic > Schedules
3. Our Staff
a. Main Page
i. Display a list of staff members. Include NAME and DESIGNATION
b. Our Staff > [Staff Name]
i. Include NAME, PICTURE, DESIGNATION, and BIO
4. Resources
a. Resources > Patient Health
i. Main Page
1. Posts (ordered by date)
a. Title
b. Summary
2. Side Navigation
a. Post Categories
ii. Patient Health > [post title]
1. Title
2. Post Category
3. Date
4. Author
5. Summary
6. Body
b. Resources > Links
1. Secondary Navigation - Categories
a. Sample Categories:
i. Local Services
ii. RDA and Drug Coverage
iii. Mental Health Resources
2. Category page
a. Include the following links in the 'Local Services' category
i. Hypertension clinics
ii. Home Care services
iii. Vaccine Clinics
c. Resources > Forms
i. Display a table with form TITLE and CATEGORY
ii. Side Navigation
1. Form Categories
a. Use the following sample Categories
i. Referrals
ii. Insurance
iii. Intake
iv. Discharge
v. Waivers
5. Alerts
a. Main page
i. List of all Alert posts
1. Include post TITLE as a link to the post
ii. Side Navigation
1. Alerts Archive
a. shown as Month + Number of posts
iii. Alerts > [Alert page]
1. Include TITLE, DATE, AUTHOR, BODY
6. Contact Us
a. Map
b. Hours of operation
c. Address
d. Phone number
e. Fax number
e. Fax number
f. Map
g. Email

Design notes:
- fixed width
- responsive (need designs for mobile, tablet, and desktop)
- simple, dark font, white background
- use Font Awesome icons where needed
- user adds own logo

Target Market(s)

Cedarline Clinics

Industry/Entity Type

Medical

Number of Pages Required

5+ page

Font styles to use
Serif
Sans Serif

Requirements
Must have
• Please keep designs very simple.
• Examples:
• https://www.quolbin.com/install
• http://www.ventrohax.com/company/about-us
• http://brindlequota.org/
• http://www.trosk.com/
Should not have
• Minimal or no use of shadows and gradients

```html
<!DOCTYPE html>
<html lang="en">
<head>
<meta charset="utf-8">
<title>Cedarline Clinics – Policies</title>
<link href="https://fonts.googleapis.com/css2?family=Open+Sans:wght@400;600;700&display=swap" rel="stylesheet">
<style>
:root{
  --blue:#0b8ce3;
  --blue-dark:#1479c9;
  --ink:#222;
  --text:#333;
  --rule:#dedede;
  --band:#f7f7f7;
  --footer:#252525;
  --footer-rule:#3d3d3d;
  --footer-text:#8c8c8c;
}
*{margin:0;padding:0;box-sizing:border-box}
html,body{width:1200px;height:1028px;overflow:hidden;background:#fff}
body{font-family:"Open Sans",Arial,sans-serif;color:var(--text);position:relative;font-size:12px}
a{color:inherit;text-decoration:none}

.topbar{position:absolute;left:0;top:0;width:1200px;height:30px;background:var(--blue);color:#fff;font-size:9.5px}
.topbar .help{position:absolute;left:162px;top:8px;white-space:nowrap}
.topbar .help span{border-left:1px solid #fff;padding-left:4px;margin-left:3px}
.topbar .links{position:absolute;right:162px;top:8px;white-space:nowrap}
.topbar .links span{border-left:1px solid #fff;padding-left:6px;margin-left:4px}

.header{position:absolute;left:0;top:30px;width:1200px;height:83px}
.brand{position:absolute;left:162px;top:27px;display:flex;align-items:center;gap:12px;white-space:nowrap}
.brand-dot{width:24px;height:24px;border-radius:50%;background:var(--blue)}
.brand-name{font-size:21px;font-weight:600;color:var(--ink)}
.nav{position:absolute;left:0;top:0;height:83px}
.nav a{position:absolute;top:0;height:83px;line-height:83px;font-size:11px;color:var(--ink);text-align:center;white-space:nowrap}
.nav a.active{background:var(--blue);color:#fff}

.crumbs{position:absolute;left:0;top:113px;width:1200px;height:59px;background:var(--band)}
.crumbs h1{position:absolute;left:162px;top:14px;font-size:11px;font-weight:700;color:var(--ink)}
.crumbs p{position:absolute;left:162px;top:33px;font-size:10px;color:var(--ink)}

.sidebar{position:absolute;left:162px;top:218px;width:201px}
.sidebar h2{font-size:11px;font-weight:700;color:var(--ink);padding-bottom:5px;border-bottom:1px solid var(--rule)}
.sidebar ul{list-style:none;margin-top:0}
.sidebar li{font-size:10px;color:var(--ink);padding-left:14px;height:22.5px;line-height:22px}
.sidebar li.current{color:var(--blue);font-weight:700}

.main{position:absolute;left:387px;top:214px;width:651px}
.main h2{font-size:14px;font-weight:600;color:var(--ink);letter-spacing:.3px;padding-bottom:4px;border-bottom:1px solid var(--rule)}
.intro{margin-top:16px;font-size:9.5px;line-height:15.2px;color:var(--ink)}
.policies{margin-top:18px}
.policy{border-bottom:1px solid var(--rule)}
.policy-head{display:flex;align-items:center;gap:15px;height:48px;margin-left:-1px}
.policy-head h3{font-size:13.5px;font-weight:600;color:var(--ink);white-space:nowrap}
.policy.open .policy-head{height:40px}
.policy-body{padding:3px 35px 20px 32px;font-size:10px;line-height:15.2px;color:var(--ink);text-align:justify}
.icon{width:18px;height:18px;flex:none}

.footer{position:absolute;left:0;top:783px;width:1200px;height:245px;background:var(--footer);border-top:4px solid var(--blue);color:var(--footer-text)}
.footer .brand{top:40px;left:162px}
.footer .brand-name{color:#fff}
.footer .brand-dot{background:#fff}
.footer-about{position:absolute;left:162px;top:84px;width:205px;font-size:9px;line-height:15px;color:#ddd}
.fcol{position:absolute;top:31px}
.fcol h4{font-size:12px;font-weight:600;color:#9a9a9a;margin-bottom:9px;white-space:nowrap}
.fcol li{list-style:none;font-size:9.5px;height:18px;white-space:nowrap}
.fcol li.here{color:#fff}
.hours li{display:flex}
.hours li span:first-child{width:91px}
.contact li{display:flex;height:15px}
.contact li span:first-child{width:89px}
.bottom{position:absolute;left:0;top:203px;width:1200px;height:38px;border-top:1px solid var(--footer-rule);font-size:10px;white-space:nowrap}
.bottom .copy{position:absolute;left:162px;top:8px}
.bottom .legal{position:absolute;left:462px;top:8px}
.bottom .legal a{margin-right:25px}
.bottom .credit{position:absolute;right:164px;top:8px}
</style>
</head>
<body>

<div class="topbar">
  <div class="help">To help Here : 250 414 7720 <span>Email : Contact@ cedarline.ca</span></div>
  <div class="links">Book an Appointment <span>Physician Toolbox</span></div>
</div>

<header class="header">
  <div class="brand"><div class="brand-dot"></div><div class="brand-name">Cedarline Clinics</div></div>
  <nav class="nav">
    <a href="#" style="left:571px">Home</a>
    <a href="#" class="active" style="left:632px;width:60px">Our Clinic</a>
    <a href="#" style="left:726px">Our Staff</a>
    <a href="#" style="left:809px">Resources</a>
    <a href="#" style="left:897px">Alerts</a>
    <a href="#" style="left:964px">Contact Us</a>
  </nav>
</header>

<section class="crumbs">
  <h1>POLICES</h1>
  <p>HOME / OUR CLINIC / POLICES</p>
</section>

<aside class="sidebar">
  <h2>OUR CLINIC</h2>
  <ul>
    <li>About</li>
    <li>Misssion</li>
    <li>Services</li>
    <li class="current">Policies</li>
    <li>Schedules</li>
  </ul>
</aside>

<main class="main">
  <h2>POLICIES</h2>
  <p class="intro">Lorem Ipsum is simply dummy text of the printing and typesetting industry. Lorem Ipsum has been the industry's standard dummy text ever since the 1500s, when an unknown printer took a galley of type and scrambled it to make a type specimen book. It has survived not only five centuries, but also the leap into electronic typesetting, remaining essentially unchanged.</p>

  <div class="policies">
    <div class="policy open">
      <div class="policy-head">
        <svg class="icon" viewBox="0 0 18 18"><circle cx="9" cy="9" r="9" fill="var(--blue-dark)"/><rect x="4.5" y="7.8" width="9" height="2.4" fill="#fff"/></svg>
        <h3>Late arrivals</h3>
      </div>
      <p class="policy-body">Lorem Ipsum is simply dummy text of the printing and typesetting industry. Lorem Ipsum has been the industry's standard dummy text ever since the 1500s, when an unknown printer took a galley of type and scrambled it to make a type specimen book. It has survived not only five centuries, but also the leap into electronic typesetting, remaining essentially unchanged.</p>
    </div>
    <div class="policy"><div class="policy-head">
      <svg class="icon" viewBox="0 0 18 18"><circle cx="9" cy="9" r="9" fill="var(--blue-dark)"/><rect x="4.5" y="7.8" width="9" height="2.4" fill="#fff"/><rect x="7.8" y="4.5" width="2.4" height="9" fill="#fff"/></svg>
      <h3>Missed appointments</h3></div></div>
    <div class="policy"><div class="policy-head">
      <svg class="icon" viewBox="0 0 18 18"><circle cx="9" cy="9" r="9" fill="var(--blue-dark)"/><rect x="4.5" y="7.8" width="9" height="2.4" fill="#fff"/><rect x="7.8" y="4.5" width="2.4" height="9" fill="#fff"/></svg>
      <h3>Fees for missed appointments</h3></div></div>
    <div class="policy"><div class="policy-head">
      <svg class="icon" viewBox="0 0 18 18"><circle cx="9" cy="9" r="9" fill="var(--blue-dark)"/><rect x="4.5" y="7.8" width="9" height="2.4" fill="#fff"/><rect x="7.8" y="4.5" width="2.4" height="9" fill="#fff"/></svg>
      <h3>Referrals and follow-ups</h3></div></div>
    <div class="policy"><div class="policy-head">
      <svg class="icon" viewBox="0 0 18 18"><circle cx="9" cy="9" r="9" fill="var(--blue-dark)"/><rect x="4.5" y="7.8" width="9" height="2.4" fill="#fff"/><rect x="7.8" y="4.5" width="2.4" height="9" fill="#fff"/></svg>
      <h3>Services not covered by RDA</h3></div></div>
    <div class="policy"><div class="policy-head">
      <svg class="icon" viewBox="0 0 18 18"><circle cx="9" cy="9" r="9" fill="var(--blue-dark)"/><rect x="4.5" y="7.8" width="9" height="2.4" fill="#fff"/><rect x="7.8" y="4.5" width="2.4" height="9" fill="#fff"/></svg>
      <h3>Information for LTF patients</h3></div></div>
    <div class="policy"><div class="policy-head">
      <svg class="icon" viewBox="0 0 18 18"><circle cx="9" cy="9" r="9" fill="var(--blue-dark)"/><rect x="4.5" y="7.8" width="9" height="2.4" fill="#fff"/><rect x="7.8" y="4.5" width="2.4" height="9" fill="#fff"/></svg>
      <h3>Medical Legal Reports</h3></div></div>
  </div>
</main>

<footer class="footer">
  <div class="brand"><div class="brand-dot"></div><div class="brand-name">Cedarline Clinics</div></div>
  <p class="footer-about">Lorem Ipsum is simply dummy text of the printing and typesetting industry. Lorem Ipsum has been the industry's standard dummy text</p>

  <div class="fcol" style="left:461px">
    <h4>Navigation</h4>
    <ul><li class="here">Home</li><li>Our Clinic</li><li>Newsletter</li><li>Our Staff</li><li>Resources</li></ul>
  </div>

  <div class="fcol hours" style="left:611px">
    <h4>Hours of Opration</h4>
    <ul>
      <li><span>Monday :</span><span>8:00 AM - 6:00 PM</span></li>
      <li><span>Tuesday :</span><span>8:00 AM - 6:00 PM</span></li>
      <li><span>Wednessday :</span><span>8:00 AM - 6:00 PM</span></li>
      <li><span>Thursday :</span><span>8:00 AM - 6:00 PM</span></li>
      <li><span>Friday :</span><span>8:00 AM - 6:00 PM</span></li>
      <li><span>Saturday :</span><span>9:00 AM - 4:00 PM</span></li>
      <li><span>Sunday :</span><span>9:00 AM - 4:00 PM</span></li>
    </ul>
  </div>

  <div class="fcol contact" style="left:836px">
    <h4>Contact Us</h4>
    <ul style="margin-left:2px">
      <li><span>Telephone :</span><span>250-414-7720</span></li>
      <li><span>Email:</span><span>contact@cedarline.ca</span></li>
      <li style="height:45px"><span>Address:</span><span>48 Alder Road<br>&nbsp;Kelowna,B. Canada,<br>&nbsp;V2B 4KD</span></li>
    </ul>
  </div>

  <div class="bottom">
    <div class="copy">© 2015 Cedarline Clinics. All Rights Reservsd</div>
    <div class="legal"><a href="#">About Us</a><a href="#">Terms of Use</a><a href="#">Privacy Policy</a></div>
    <div class="credit">Site design &amp; developed by Lumora Web Studio</div>
  </div>
</footer>

</body>
</html>
```